Business Card for a mobile physiotherapy company

I need a layout for a business card for a mobile physiotherapy company.
Slogan is "Mobile Physiotherapy - Your Road To Recovery"
Phone number is 867-555-0142
Email VardenTherapy@postnest.ca (subject to change with website)
Website www.VardenTherapy.ca
My name and credentials: Luke Varden Luke Varden, BSc(kin), MPT, CAFCI, IMS
Information maybe included: Direct Billing, Services including Physiotherapy, IMS, acupuncture
Maybe include facebook and instagram logos
One side with the logo clean and sharp
Other side with details, try not to look too busy, keep everything concise

```html
<!DOCTYPE html>
<html lang="en">
<head>
<meta charset="utf-8">
<title>Varden Therapy – Business Card</title>
<link rel="stylesheet" href="https://fonts.googleapis.com/css2?family=Noto+Serif:ital,wght@0,400;0,700;1,400&display=swap">
<style>
  :root {
    --page-bg: #d9dadb;
    --card-white: #f4f4f2;
    --navy: #24466e;
    --forest: #1f5a4a;
    --band: #2a4472;
    --text-light: #f2f4f6;
    --text-soft: #d6dde6;
  }
  * { box-sizing: border-box; margin: 0; padding: 0; }
  html, body {
    width: 1200px; height: 576px; overflow: hidden;
    background: var(--page-bg);
    font-family: "Noto Serif", Georgia, serif;
  }
  .canvas { position: relative; width: 1200px; height: 576px; }

  .card {
    position: absolute; top: 138px;
    width: 484px; height: 292px;
    border-radius: 12px; overflow: hidden;
    background: var(--card-white);
  }

  /* Front */
  .card--front { left: 82px; }
  .brand-name {
    position: absolute; left: 0; right: 0;
    text-align: center; color: var(--navy);
    font-weight: 400; line-height: 1; white-space: nowrap;
  }
  .card--front .brand-name { top: 106px; font-size: 36px; }
  .services {
    position: absolute; left: 0; right: 0; top: 259px;
    text-align: center; font-size: 12.5px; color: var(--navy); white-space: nowrap;
  }
  .front-stripe {
    position: absolute; left: 0; right: 0; bottom: 0; height: 6px;
    background: linear-gradient(90deg, var(--forest), var(--navy));
  }

  /* Back */
  .card--back { left: 602px; width: 480px; height: 291px; }
  .back-shape { position: absolute; inset: 0; }
  .contact { position: absolute; left: 20px; top: 0; color: var(--text-light); }
  .contact__name { position: absolute; top: 36px; font-size: 21px; font-weight: 700; letter-spacing: 0.3px; white-space: nowrap; }
  .contact__creds { position: absolute; top: 64px; font-size: 12px; color: var(--text-soft); white-space: nowrap; }
  .contact__follow { position: absolute; top: 138px; font-size: 13px; white-space: nowrap; }
  .contact__list { position: absolute; top: 165px; list-style: none; }
  .contact__item { display: flex; align-items: center; height: 17.5px; font-size: 13px; white-space: nowrap; }
  .contact__icon { width: 11px; height: 11px; margin-right: 12px; fill: var(--text-light); flex: none; }
  .slogan {
    position: absolute; left: 0; top: 235px; width: 282px; height: 35px;
    background: var(--band); color: var(--text-light);
    font-style: italic; font-size: 12.5px; white-space: nowrap;
    display: flex; align-items: center; padding-left: 20px;
  }
  .card--back .brand-name { left: 290px; right: 0; top: 134px; font-size: 20px; }
</style>
</head>
<body>
<main class="canvas">

  <section class="card card--front" aria-label="Card front">
    <p class="brand-name">Varden Therapy</p>
    <p class="services">Direct Billing &nbsp;|&nbsp; Services Including Physiotherapy &nbsp;|&nbsp; IMS &nbsp;|&nbsp; Acupuncture</p>
    <div class="front-stripe"></div>
  </section>

  <section class="card card--back" aria-label="Card back">
    <svg class="back-shape" width="480" height="291" viewBox="0 0 480 291" aria-hidden="true">
      <defs>
        <linearGradient id="panelGrad" x1="0" y1="0" x2="0" y2="1">
          <stop offset="0" stop-color="#26446b"/>
          <stop offset="1" stop-color="#1e5652"/>
        </linearGradient>
      </defs>
      <rect width="480" height="291" fill="url(#panelGrad)"/>
      <path d="M304 0 C268 80 262 200 300 291 L480 291 L480 0 Z" fill="#f4f4f2"/>
      <path d="M304 0 C268 80 262 200 300 291" fill="none" stroke="#1f5a4a" stroke-width="2"/>
    </svg>

    <div class="contact">
      <h1 class="contact__name">LUKE VARDEN</h1>
      <p class="contact__creds">BSc(kin), MPT, CAFCI, IMS</p>
      <p class="contact__follow">Follow us on: @VardenTherapy</p>
      <ul class="contact__list">
        <li class="contact__item">
          <svg class="contact__icon" viewBox="0 0 12 12"><path d="M1 4.5C1 2.5 3.5 1.5 6 1.5S11 2.5 11 4.5H8.5V3.5H3.5V4.5ZM2.5 6h7l1 4.5h-9Z"/></svg>
          867-555-0142
        </li>
        <li class="contact__item">
          <svg class="contact__icon" viewBox="0 0 12 12"><path d="M1 2.5h10v7H1Zm1 1v.3L6 6.6l4-2.8v-.3Zm0 1.5v3.5h8V5L6 7.8Z"/></svg>
          VardenTherapy@postnest.ca
        </li>
        <li class="contact__item">
          <svg class="contact__icon" viewBox="0 0 12 12"><circle cx="6" cy="6" r="5" fill="none" stroke="#f2f4f6" stroke-width="1"/><ellipse cx="6" cy="6" rx="2.2" ry="5" fill="none" stroke="#f2f4f6" stroke-width="1"/><path d="M1 6h10" stroke="#f2f4f6" stroke-width="1"/></svg>
          www.VardenTherapy.ca
        </li>
      </ul>
    </div>

    <p class="slogan">Mobile Physiotherapy - Your Road To Recovery</p>

    <p class="brand-name">Varden Therapy</p>
  </section>

</main>
</body>
</html>
```